Visitenkarten und Briefpapier
Zielgruppe
Planung und Realisierung von individuellen und wertbeständigen Kamin- und Ofenlösungen, sowie Fliesen- und Baddesign.
Aufgabenstellung
Wir benötigen ein möglichst schlichtes Design für Visitenkarten, bzw. Briefpapier. Für die Visitenkarten gerne auch Vorschläge mit Prägung, Ausstanzung oder mit Heißfolie. Auch Klappkarten wären denkbar. Das Design soll "das gewisse Etwas haben" und nicht zu verspielt sein.
Die Visitenkarten sind für die Firma KORVA, das Logo von der Ausstellung "raumfunke" soll dezent mit eingebunden werden (bei dem Briefpapier z.B. in der Fußzeile". Die farbliche Gestaltung sollte sich an den Farben des Logos orientieren.
Schriftart für Texte: Century Gothic
Schriftfarbe: RAL 7016
Nur eine Idee: Ich könnte mir auch gut vorstellen, dass die Visitenkarte aus einer Zündholzverpackung (wenn dann aber eine besondere mit nur einem Zündholz oder einem besonders breiten) besteht: http://glimmvelo.de/produkte_briefchen.php

```html
<!DOCTYPE html>
<html lang="de">
<head>
<meta charset="utf-8">
<title>Korva Briefpapier</title>
<link href="https://fonts.googleapis.com/css2?family=Questrial&display=swap" rel="stylesheet">
<style>
  :root {
    --backdrop: #ece9e4;
    --paper: #ffffff;
    --ink: #2b3338;
    --logo-ink: #111111;
    --accent: #f08a00;
    --footer: #24353b;
    --footer-ink: #ffffff;
  }
  * { margin: 0; padding: 0; box-sizing: border-box; }
  html, body {
    width: 1200px; height: 1120px; overflow: hidden;
    background: var(--backdrop);
    font-family: "Questrial", "Century Gothic", sans-serif;
    color: var(--ink);
  }
  .sheet {
    position: absolute; left: 218px; top: 20px;
    width: 764px; height: 1080px;
    background: var(--paper);
  }
  .brand { position: absolute; right: 31px; top: 26px; text-align: right; }
  .brand-name {
    font-size: 64px; line-height: 60px; letter-spacing: 2px;
    color: var(--logo-ink);
  }
  .brand-tagline { font-size: 15.5px; margin-top: 4px; color: var(--ink); }
  .contact {
    position: absolute; left: 574px; top: 138px;
    font-size: 14px; line-height: 17.6px;
  }
  .contact .spaced { letter-spacing: 1.3px; }
  .contact .gap { margin-top: 3px; }
  .contact .label { display: inline-block; width: 38px; }
  .exhibit {
    position: absolute; right: 36px; top: 248px;
    font-size: 10.5px; color: var(--ink);
  }
  .sender-line {
    position: absolute; left: 97px; top: 195px;
    font-size: 8.5px; letter-spacing: 0.8px;
  }
  .sender-line::before {
    content: ""; display: inline-block; width: 4px; height: 4px;
    background: var(--accent); margin-right: 6px; vertical-align: 1px;
  }
  .corner-mark {
    position: absolute; width: 4px; height: 4px; background: var(--accent); top: 348px;
  }
  .fold-mark { position: absolute; left: 0; }
  .footer {
    position: absolute; left: 0; bottom: 0; width: 100%; height: 101px;
    background: var(--footer); color: var(--footer-ink);
  }
  .legal { position: absolute; left: 74px; top: 24px; font-size: 9.4px; line-height: 13px; }
  .legal .company { font-size: 11.5px; line-height: 15px; }
  .banking {
    position: absolute; right: 33px; top: 11px;
    font-size: 9.2px; line-height: 13.7px; text-align: right;
  }
</style>
</head>
<body>
  <main class="sheet">
    <header class="brand">
      <div class="brand-name">KORVA</div>
      <div class="brand-tagline">kamine · öfen · fliesen</div>
    </header>

    <address class="contact" style="font-style:normal">
      <div class="spaced">Am Kiesgrund 5</div>
      <div class="spaced">34512 Lindhagen</div>
      <div><span class="label">fon:</span> 05612 / 40 17 30</div>
      <div><span class="label">fax:</span> 05612 / 40 17 38</div>
      <div class="gap">info@korva-lindhagen.de</div>
      <div>www.korva-lindhagen.de</div>
    </address>
    <div class="exhibit">raumfunke</div>

    <div class="sender-line">Korva GmbH &nbsp;|&nbsp; Am Kiesgrund 5 &nbsp;|&nbsp; 34512 Lindhagen</div>

    <span class="corner-mark" style="left:75px"></span>
    <span class="corner-mark" style="left:382px"></span>

    <svg class="fold-mark" style="top:375px" width="8" height="14" viewBox="0 0 8 14"><polygon points="0,0 8,7 0,14" fill="var(--accent)"/></svg>
    <svg class="fold-mark" style="top:757px" width="8" height="14" viewBox="0 0 8 14"><polygon points="0,0 8,7 0,14" fill="var(--accent)"/></svg>

    <footer class="footer">
      <div class="legal">
        <div class="company">Korva GmbH</div>
        <div>Geschäftsführer: Jonas Beispiel</div>
        <div>Amtsgericht Lindhagen: 1 HRB 482</div>
        <div>Ust-ID.Nr.: DE 314159260</div>
        <div>Steuernummer: 027 318 40962</div>
      </div>
      <div class="banking">
        <div>Bankverbindung 1:</div>
        <div>BIC: KRVADEF1LIN</div>
        <div>IBAN: DE21 38410 0007 0000 0081 36</div>
        <div>Bankverbindung 2:</div>
        <div>BIC: KRVADEF1LIN</div>
        <div>IBAN: DE21 38410 0007 0000 0081 36</div>
      </div>
    </footer>
  </main>
</body>
</html>
```